Website for a Steadwell, an HVAC company.

We are a company that provides residential and commercial service. We don’t need any widgets other than a call to action where customers can message us. Though we have very few google reviews, they are all great and would like to see those populated. Simple and modern is the style. I included our logo and a pic of our vans.

Target Market(s)

Residential customers

Coding

Coded - Design and coding required

Number of Pages Required

1 page

Font styles to use
Sans Serif

Colors
0054AA
0677BA
7BADD7
CADEEF
E8F1F8
EE7325
F08F49
F5BC92
FAE3D3
FDF4ED

```html
<!DOCTYPE html>
<html lang="en">
<head>
<meta charset="utf-8">
<title>Steadwell Heating and Air</title>
<link href="https://fonts.googleapis.com/css2?family=Poppins:wght@400;500;600;700;800&family=Open+Sans:wght@400;600;700&display=swap" rel="stylesheet">
<style>
:root{
  --blue-deep:#0054AA;
  --blue:#0677BA;
  --blue-mid:#7BADD7;
  --blue-light:#CADEEF;
  --blue-pale:#E8F1F8;
  --orange:#EE7325;
  --orange-mid:#F08F49;
  --orange-soft:#F5BC92;
  --orange-light:#FAE3D3;
  --orange-pale:#FDF4ED;
  --ink:#1d2433;
  --muted:#5f6b7a;
  --white:#ffffff;
}
*{box-sizing:border-box;margin:0;padding:0}
html,body{width:1200px;height:4332px;overflow:hidden}
body{font-family:"Open Sans",Arial,sans-serif;color:var(--ink);background:var(--white);position:relative}
h1,h2,h3,.btn,.nav a{font-family:"Poppins",Arial,sans-serif}
.abs{position:absolute}
.btn{display:inline-block;border-radius:20px;padding:10px 24px;font-size:13px;font-weight:600;color:var(--white);letter-spacing:.5px;text-decoration:none}
.btn-orange{background:var(--orange)}
.btn-blue{background:var(--blue)}
.photo{position:absolute}

/* header */
.site-header{position:absolute;top:0;left:0;width:1200px;height:88px;background:var(--white);z-index:5}
.brand{position:absolute;left:130px;top:0;width:260px;height:110px;background:var(--white);border-radius:0 0 60px 60px;display:flex;align-items:center;justify-content:center;gap:10px;z-index:6}
.brand-dot{width:30px;height:30px;border-radius:50%;background:var(--orange)}
.brand-name{font-family:"Poppins",sans-serif;font-weight:700;font-size:26px;color:var(--blue-deep)}
.nav{position:absolute;left:430px;top:30px;display:flex;gap:34px}
.nav a{font-size:13px;font-weight:600;color:var(--ink);text-decoration:none}
.nav a.active{color:var(--blue-deep);border-bottom:2px solid var(--orange);padding-bottom:4px}
.site-header .btn{position:absolute;left:935px;top:20px;padding:10px 22px;font-size:12px}

/* hero */
.hero{position:absolute;top:88px;left:0;width:1200px;height:700px;overflow:hidden}
.hero .photo{inset:0;background:linear-gradient(180deg,#2d3c63 0%,#7a5a6a 38%,#e08a45 62%,#3a3140 100%)}
.hero h1{position:absolute;left:150px;top:140px;color:var(--white);font-weight:800;font-size:60px;line-height:1.05}
.hero .btn{position:absolute;left:150px;top:285px}
.slide-arrow{position:absolute;width:34px;height:34px;border-radius:50%;background:rgba(255,255,255,.85);display:flex;align-items:center;justify-content:center}
.dots{position:absolute;left:560px;top:500px;display:flex;gap:10px}
.dots span{width:8px;height:8px;border-radius:50%;background:rgba(255,255,255,.6)}
.dots span.on{background:var(--white)}
.hero-wave{position:absolute;left:0;top:560px}

/* about */
.about{position:absolute;top:788px;left:0;width:1200px;height:440px}
.about-mark{position:absolute;left:150px;top:40px;width:330px;height:330px;display:flex;align-items:center;justify-content:center;gap:14px}
.about-mark .brand-dot{width:60px;height:60px}
.about-mark .brand-name{font-size:48px}
.about h2{position:absolute;left:592px;top:20px;font-size:34px;font-weight:800;color:var(--blue-deep)}
.about h2 span,.accent{color:var(--orange)}
.about h3{position:absolute;left:592px;top:68px;font-size:22px;font-weight:600;color:var(--blue-deep);line-height:1.25;width:420px}
.about p{position:absolute;left:592px;top:138px;width:400px;font-size:12.5px;line-height:1.7;color:var(--muted)}
.about .btn{position:absolute;left:592px;top:318px}
.ghost-vert{position:absolute;font-family:"Poppins",sans-serif;font-weight:800;color:rgba(0,84,170,.08);transform:rotate(-90deg);transform-origin:left top;white-space:nowrap}

/* services */
.services-band{position:absolute;top:1210px;left:0;width:1200px;height:240px}
.ghost{position:absolute;font-family:"Poppins",sans-serif;font-weight:800;color:rgba(0,84,170,.08);white-space:nowrap}
.section-title{position:absolute;width:1200px;text-align:center;font-size:38px;font-weight:700;color:var(--blue-deep)}
.services{position:absolute;top:1448px;left:0;width:1200px;height:392px;display:grid;grid-template-columns:repeat(4,300px)}
.service{position:relative;overflow:hidden}
.service .photo{inset:0}
.service-card{position:absolute;left:6px;width:288px;height:100px;padding:18px 20px;color:var(--white)}
.service-card h3{font-size:20px;font-weight:600;line-height:1.2}
.service-card small{display:block;font-size:11px;font-weight:700;margin-top:6px;text-decoration:underline}
.service-card .go{position:absolute;right:18px;top:18px}
.card-blue{background:var(--blue);top:6px}
.card-orange{background:var(--orange);bottom:6px}

/* clean air */
.clean{position:absolute;top:1840px;left:0;width:1200px;height:560px;overflow:hidden}
.clean .photo{inset:0;background:linear-gradient(90deg,#f6efe8 0%,#f1e2d4 45%,#e9eef3 100%)}
.clean h2{position:absolute;width:1200px;text-align:center;font-weight:800;font-size:38px;line-height:1.2}
.clean p{position:absolute;left:400px;top:220px;width:400px;text-align:center;font-size:12.5px;line-height:1.7;color:var(--muted)}
.clean .btn{position:absolute;left:535px;top:356px}
.van{position:absolute;left:740px;top:2160px;width:400px;height:250px;background:linear-gradient(160deg,#1d2a44,#0b1424);border-radius:30px 50px 16px 16px;z-index:3}

/* testimonials */
.testimonials{position:absolute;top:2320px;left:0;width:1200px;height:690px;background:linear-gradient(180deg,#3aaee8 0%,var(--blue) 70%,var(--blue-deep) 100%);overflow:hidden}
.testimonials .ghost{color:rgba(255,255,255,.12);left:90px;top:175px;font-size:96px}
.testimonials h2{position:absolute;width:1200px;text-align:center;top:280px;color:var(--white);font-size:38px;font-weight:700}
.quote-mark{position:absolute;left:570px;top:350px}
.testimonials blockquote{position:absolute;left:200px;top:428px;width:800px;text-align:center;color:var(--white);font-style:italic;font-size:14px;line-height:1.7}
.reviewer{position:absolute;width:1200px;top:530px;text-align:center;color:var(--white);font-family:"Poppins",sans-serif;font-weight:600;font-size:17px}
.stars{color:#f5b400;letter-spacing:3px;margin-left:10px}

/* video */
.video{position:absolute;top:3000px;left:0;width:1200px;height:530px;overflow:hidden}
.video .photo{inset:0;background:linear-gradient(135deg,#9ea4a6 0%,#6f7a80 45%,#2f4e8a 100%)}
.play{position:absolute;left:556px;top:96px}

/* contact */
.contact-bg{position:absolute;top:3500px;left:0;width:1200px;height:832px;background:linear-gradient(180deg,#1f8fd8 0%,var(--blue-deep) 100%)}
.contact-card{position:absolute;top:3392px;left:152px;width:896px;height:560px;background:var(--white);z-index:2}
.contact-card .ghost{left:90px;top:10px;font-size:96px}
.contact-card h2{position:absolute;width:896px;text-align:center;top:72px;font-size:38px;font-weight:700;color:var(--blue-deep)}
.form{position:absolute;left:88px;top:170px;width:720px}
.row{display:flex;gap:16px;margin-bottom:12px}
.field{flex:1;height:52px;border:1px solid #c9ced6;border-radius:4px;padding:16px 14px;font-size:13px;color:#555}
.field.message{height:112px}
.form .btn{display:block;width:130px;margin:30px auto 0;text-align:center}

/* footer */
.site-footer{position:absolute;top:3980px;left:0;width:1200px;height:352px;color:var(--white);z-index:2}
.foot-col{position:absolute;top:20px}
.foot-col h4{font-family:"Poppins",sans-serif;font-size:15px;font-weight:700;margin-bottom:14px;letter-spacing:.5px}
.foot-col ul{list-style:none;font-size:13px;line-height:1.75}
.areas{left:168px;border-left:2px solid var(--orange);padding-left:18px}
.areas .cols{display:flex;gap:56px}
.contact-info{left:560px;border-left:2px solid var(--orange);padding-left:18px}
.contact-info li{display:flex;gap:10px;align-items:flex-start}
.contact-info svg{margin-top:4px;flex:none}
.menus{left:912px;border-left:2px solid var(--orange);padding-left:18px}
.foot-bar{position:absolute;top:270px;left:0;width:1200px;border-top:1px solid rgba(255,255,255,.25);padding-top:20px}
.foot-bar p{position:absolute;left:168px;top:22px;font-size:12px}
.social{position:absolute;left:800px;top:16px;display:flex;gap:10px}
.social span{width:28px;height:28px;border-radius:50%;background:rgba(255,255,255,.9)}
</style>
</head>
<body>

<header class="site-header">
  <div class="brand"><span class="brand-dot"></span><span class="brand-name">Steadwell</span></div>
  <nav class="nav">
    <a class="active" href="#">HOME</a>
    <a href="#">OUR SERVICES</a>
    <a href="#">ABOUT US</a>
    <a href="#">REVIEWS</a>
    <a href="#">CONTACT US</a>
  </nav>
  <a class="btn btn-orange" href="#">BOOK ONLINE</a>
</header>

<section class="hero">
  <div class="photo" role="img" aria-label="Cable-stayed bridge over water at sunset"></div>
  <h1>YOUR COMFORT<br>IS OUR MISSION</h1>
  <a class="btn btn-blue" href="#">GET STARTED ➔</a>
  <span class="slide-arrow" style="left:84px;top:248px"><svg width="12" height="12" viewBox="0 0 12 12"><path d="M8 1 3 6l5 5" stroke="#333" stroke-width="2" fill="none"/></svg></span>
  <span class="slide-arrow" style="left:1082px;top:248px"><svg width="12" height="12" viewBox="0 0 12 12"><path d="M4 1l5 5-5 5" stroke="#333" stroke-width="2" fill="none"/></svg></span>
  <div class="dots"><span class="on"></span><span></span><span></span><span></span></div>
  <svg class="hero-wave" width="1200" height="140" viewBox="0 0 1200 140">
    <path d="M0 70 C300 10 700 10 1200 50 L1200 140 L0 140Z" fill="var(--blue-mid)"/>
    <path d="M0 90 C300 30 700 30 1200 70 L1200 140 L0 140Z" fill="var(--orange)"/>
    <path d="M0 104 C300 50 700 50 1200 88 L1200 140 L0 140Z" fill="var(--blue)"/>
    <path d="M0 118 C300 70 700 70 1200 104 L1200 140 L0 140Z" fill="var(--white)"/>
  </svg>
</section>

<section class="about">
  <div class="about-mark"><span class="brand-dot"></span><span class="brand-name">Steadwell</span></div>
  <h2>ABOUT <span>US</span></h2>
  <h3>Heating and Air Conditioning Services You Can Depend On</h3>
  <p>Since 2003, Steadwell Heating and Air has provided reliable and affordable heating and cooling solutions in Charleston, SC, and the surrounding areas. With over 20 years of experience, we have earned the trust of our community by delivering top-notch HVAC services. Contact us today at (843) 555-0142.</p>
  <a class="btn btn-orange" href="#">READ MORE ➔</a>
  <div class="ghost-vert" style="left:1130px;top:240px;font-size:62px">ABOUT</div>
</section>

<section class="services-band">
  <svg class="abs" style="left:0;top:0" width="1200" height="240" viewBox="0 0 1200 240">
    <path d="M0 60 C350 0 800 110 1200 40 L1200 240 L0 240Z" fill="var(--blue-pale)"/>
    <path d="M0 60 C350 0 800 110 1200 40" stroke="var(--blue-light)" stroke-width="4" fill="none"/>
  </svg>
  <div class="ghost" style="left:90px;top:90px;font-size:96px">SERVICES</div>
  <h2 class="section-title" style="top:122px">OUR <span class="accent">SERVICES</span></h2>
</section>

<section class="services">
  <div class="service">
    <div class="photo" role="img" aria-label="Technician servicing an outdoor heating unit" style="background:linear-gradient(160deg,#b9aea4,#6e6d70)"></div>
    <div class="service-card card-orange"><h3>Heating Repair</h3><small>BOOK NOW</small></div>
  </div>
  <div class="service">
    <div class="photo" role="img" aria-label="Hand cleaning an air vent" style="background:linear-gradient(160deg,#cfd7de,#8aa4b8)"></div>
    <div class="service-card card-blue"><h3>Heating<br>Maintenance</h3><small>BOOK NOW</small>
      <svg class="go" width="22" height="22" viewBox="0 0 22 22"><circle cx="11" cy="11" r="10" stroke="#fff" stroke-width="2" fill="none"/><path d="M6 11h10M12 7l4 4-4 4" stroke="#fff" stroke-width="2" fill="none"/></svg></div>
  </div>
  <div class="service">
    <div class="photo" role="img" aria-label="Technician repairing an air conditioner" style="background:linear-gradient(160deg,#8a6a4e,#3e4a5c)"></div>
    <div class="service-card card-orange"><h3>AC Repair</h3><small>BOOK NOW</small>
      <svg class="go" width="22" height="22" viewBox="0 0 22 22"><circle cx="11" cy="11" r="10" stroke="#fff" stroke-width="2" fill="none"/><path d="M6 11h10M12 7l4 4-4 4" stroke="#fff" stroke-width="2" fill="none"/></svg></div>
  </div>
  <div class="service">
    <div class="photo" role="img" aria-label="Technician inspecting an AC unit" style="background:linear-gradient(160deg,#9fb3c6,#5c6f86)"></div>
    <div class="service-card card-blue"><h3>AC Maintenance</h3><small>BOOK NOW</small>
      <svg class="go" width="22" height="22" viewBox="0 0 22 22"><circle cx="11" cy="11" r="10" stroke="#fff" stroke-width="2" fill="none"/><path d="M6 11h10M12 7l4 4-4 4" stroke="#fff" stroke-width="2" fill="none"/></svg></div>
  </div>
</section>

<section class="clean">
  <div class="photo" role="img" aria-label="Couple relaxing at home with clean air"></div>
  <h2 style="top:90px;color:var(--blue)">CLEAN AIR QUALITY</h2>
  <h2 style="top:136px;color:var(--orange)">EQUALS A HAPPY HOME</h2>
  <p>If your home smells stuffy due to poor air quality, consider upgrading your air filters or adding a purifier. We are happy to help you choose products that improve your comfort and your family's quality of life. Remember, clean air helps you feel your best every single day.</p>
  <a class="btn btn-orange" href="#">READ MORE ➔</a>
  <div class="ghost-vert" style="left:1130px;top:420px;font-size:62px">HAPPY HOME</div>
</section>

<section class="testimonials">
  <svg class="abs" style="left:0;top:0" width="1200" height="150" viewBox="0 0 1200 150">
    <path d="M0 0 H1200 V60 C800 140 400 20 0 100Z" fill="#f3ece6"/>
    <path d="M0 100 C400 20 800 140 1200 60" stroke="var(--white)" stroke-width="10" fill="none"/>
  </svg>
  <div class="ghost">TESTIMONIALS</div>
  <h2>CUSTOMER TESTIMONIALS</h2>
  <svg class="quote-mark" width="60" height="46" viewBox="0 0 60 46"><path d="M4 40c0-16 6-28 20-34l3 5c-8 4-11 10-11 16h10v13zM34 40c0-16 6-28 20-34l3 5c-8 4-11 10-11 16h10v13z" fill="none" stroke="#fff" stroke-width="2.5"/></svg>
  <span class="slide-arrow" style="left:110px;top:466px"><svg width="12" height="12" viewBox="0 0 12 12"><path d="M8 1 3 6l5 5" stroke="#333" stroke-width="2" fill="none"/></svg></span>
  <span class="slide-arrow" style="left:1046px;top:466px"><svg width="12" height="12" viewBox="0 0 12 12"><path d="M4 1l5 5-5 5" stroke="#333" stroke-width="2" fill="none"/></svg></span>
  <blockquote>"This was my first time using Steadwell Heating and Air and I was extremely impressed with the prompt service and fair pricing. As a property manager, I work with a lot of contractors and these are two things that can be hard to find. I'm looking forward to working with them more in the future!"</blockquote>
  <div class="reviewer">- Maria T <span class="stars">★★★★★</span></div>
</section>

<div class="van" role="img" aria-label="Company service van"></div>

<section class="video">
  <div class="photo" role="img" aria-label="Technician in a cap working on an outdoor AC unit"></div>
  <svg class="play" width="88" height="88" viewBox="0 0 88 88"><circle cx="44" cy="44" r="44" fill="#e02424"/><path d="M35 28l26 16-26 16z" fill="#fff"/></svg>
</section>

<div class="contact-bg"></div>

<section class="contact-card">
  <div class="ghost">CONTACT</div>
  <h2>CONTACT <span class="accent">US</span></h2>
  <form class="form">
    <div class="row"><div class="field">First Name</div><div class="field">Last Name</div></div>
    <div class="row"><div class="field">Email address</div><div class="field">Phone Number</div></div>
    <div class="row"><div class="field message">Message</div></div>
    <span class="btn btn-orange">SUBMIT ➔</span>
  </form>
</section>

<footer class="site-footer">
  <div class="foot-col areas">
    <h4>AREAS WE SERVE</h4>
    <div class="cols">
      <ul><li>Charleston</li><li>Mount Pleasant</li><li>Folly Beach</li><li>Summerville</li><li>Isle of Palms</li></ul>
      <ul><li>North Charleston</li><li>Sullivan's Island</li><li>Goose Creek</li><li>James Island</li><li>Johns Island</li></ul>
    </div>
  </div>
  <div class="foot-col contact-info">
    <h4>CONTACT US</h4>
    <ul>
      <li><svg width="12" height="12" viewBox="0 0 12 12"><path d="M2 1h3l1 3-2 1c1 2 2 3 3 3l1-2 3 1v3c-6 0-9-3-9-9z" fill="var(--orange)"/></svg>(843) 555-0142</li>
      <li><svg width="12" height="12" viewBox="0 0 12 12"><rect x="1" y="2" width="10" height="8" fill="var(--orange)"/><path d="M1 2l5 4 5-4" stroke="#fff" fill="none"/></svg>hello@steadwellair.com</li>
      <li><svg width="12" height="12" viewBox="0 0 12 12"><circle cx="6" cy="6" r="5" fill="var(--orange)"/><path d="M6 3v3h2" stroke="#fff" fill="none"/></svg>Mon - Fri: 7:00am - 6:00pm<br>Saturday: 8:00am - 3:00pm<br>Sunday: Appointment Only<br>License #40217</li>
    </ul>
  </div>
  <div class="foot-col menus">
    <h4>MENUS</h4>
    <ul><li>Our services</li><li>Heating</li><li>Cooling</li><li>Energy Saving Products</li><li>Contact Us</li></ul>
  </div>
  <div class="foot-bar">
    <p>© 2025 Steadwell Heating and Air All Rights Reserved &nbsp;|&nbsp; Privacy Policy &nbsp;|&nbsp; Terms of Use</p>
    <div class="social"><span></span><span></span><span></span></div>
  </div>
</footer>

</body>
</html>
```